Stylish new business card needed!

Hello everyone! I am in need of a new business card design for an alarm company here in Hurricane WV. I have all fonts, color codes and logos provided for you use! We are a young company and like the style of a clean sleek looking business card. Would like it double sided, one side holding the logo and the other with your design!
Target Market(s)
The people that are looking for the newest tech for home automation and security
Industry/Entity Type
Alarm services; Home automation
Contact Information for Business Card
Name of person; position (Sales; Installer); Phone Number (555.418.7260); Employee cell Number; Website (www.GuardedByVelk.example); Employee Email; Double sided
Look and feel
Each slider illustrates characteristics of the customer's brand and the style your logo design should communicate.

```html
<!DOCTYPE html>
<html lang="en">
<head>
<meta charset="utf-8">
<title>Velk Business Card</title>
<link rel="stylesheet" href="https://fonts.googleapis.com/css2?family=Montserrat:wght@400;500;700&display=swap">
<style>
  :root {
    --backdrop: #c9c9c9;
    --card: #9a9a9a;
    --accent: #f28c4a;
    --ink: #ffffff;
  }
  * { margin: 0; padding: 0; box-sizing: border-box; }
  html, body {
    width: 1200px; height: 788px; overflow: hidden;
    background: var(--backdrop);
    font-family: "Montserrat", Arial, sans-serif;
  }
  .stage {
    width: 1200px; height: 788px;
    display: flex; align-items: center; justify-content: center; gap: 60px;
  }
  .card {
    position: relative;
    width: 520px; height: 300px;
    border-radius: 26px;
    background: var(--card);
    color: var(--ink);
    overflow: hidden;
  }
  .wordmark {
    display: flex; align-items: center; gap: 12px;
    font-weight: 500; letter-spacing: 0.06em;
    color: var(--ink);
  }
  .wordmark-dot {
    border-radius: 50%;
    background: var(--accent);
  }
  /* Front side */
  .card-front .wordmark {
    position: absolute; left: 40px; bottom: 46px;
    font-size: 56px;
  }
  .card-front .wordmark-dot { width: 16px; height: 16px; }
  .divider {
    position: absolute; left: 268px; top: 40px; bottom: 40px;
    width: 1px; background: var(--accent);
  }
  .contact {
    position: absolute; left: 290px; top: 44px; right: 16px;
    font-size: 12.5px; line-height: 1.55;
  }
  .contact-name {
    color: var(--accent); font-weight: 700;
    font-size: 19px; letter-spacing: 0.08em; text-transform: uppercase;
    line-height: 1.1;
  }
  .contact-role { margin-bottom: 10px; font-size: 13px; }
  .contact-line { display: flex; align-items: center; gap: 7px; white-space: nowrap; }
  .contact-line svg { width: 11px; height: 11px; flex: none; }
  .contact-address { margin-top: 4px; }
  /* Back side */
  .card-back { display: flex; align-items: center; justify-content: center; }
  .card-back .wordmark { font-size: 92px; gap: 18px; }
  .card-back .wordmark-dot { width: 24px; height: 24px; }
</style>
</head>
<body>
<main class="stage">
  <section class="card card-front" aria-label="Card front">
    <div class="wordmark"><span class="wordmark-dot"></span>VELK</div>
    <div class="divider"></div>
    <div class="contact">
      <div class="contact-name">Daniel Brooks</div>
      <div class="contact-role">Sales/Installer</div>
      <div class="contact-line">
        <svg viewBox="0 0 12 12" aria-hidden="true"><path fill="var(--accent)" d="M2.4 0.8l2 2-1 1.3c.7 1.6 1.9 2.8 3.5 3.5l1.3-1 2 2-1.3 1.6C5 10.2 1.8 7 0.8 2.1z"/></svg>
        555.418.7260
      </div>
      <div class="contact-line">
        <svg viewBox="0 0 12 12" aria-hidden="true"><rect x="0.5" y="2" width="11" height="8" rx="1" fill="var(--accent)"/><path d="M1 2.6l5 4 5-4" stroke="var(--card)" stroke-width="1" fill="none"/></svg>
        info@GuardedByVelk.example
      </div>
      <div class="contact-line">
        <svg viewBox="0 0 12 12" aria-hidden="true"><circle cx="6" cy="6" r="5.5" fill="var(--accent)"/><path d="M0.5 6h11M6 0.5c-2.5 3-2.5 8 0 11M6 0.5c2.5 3 2.5 8 0 11" stroke="var(--card)" stroke-width="0.8" fill="none"/></svg>
        www.GuardedByVelk.example
      </div>
      <div class="contact-address">1480 W Harlan Avenue<br>Milford County Name 4127</div>
    </div>
  </section>
  <section class="card card-back" aria-label="Card back">
    <div class="wordmark"><span class="wordmark-dot"></span>VELK</div>
  </section>
</main>
</body>
</html>
```